Vernac Law Business cards and stationary design project

We are looking for a stationary design for business cards (double sided), 8x10, 5x7, and legal and standard envelopes.

We would like the design to match the logo that we have already.
Color palate preferred is Teal, White, grey and any others that will look good for a professional law firm.

We would like this statement: "RELATIONSHIPS. RESPECT. RESULT" to be on the back of the business cards and maybe on the stationary if it looks good.

Please see link to website for more information: www.vernac-law.example

Target Market(s)

Potential clients that need Attorney services.

Industry/Entity Type

Law Firm

Contact Information for Business Card

We would like the front and back to be two different colors. Current business cards are teal front, grey back and are a vertical design. We are open to options with colors.

Font styles to use
Serif

Colors
33a6d7
33b8a4
b9b9b9
5c5c5c

Requirements
Must have
• Logo supplied needs to go on the card and stationary.
• Match website color palate, www.vernac-law.example
• Be professional and not too wordy.
• Criminal Law, Civil Litigation, Personal Injury, Restraining Orders need to be on the card.
Nice to have
• RELATIONSHIPS. RESPECT. RESULTS. on the back of the card.
Should not have
• Not be too busy/wordy or too flashy.

```html
<!DOCTYPE html>
<html lang="en">
<head>
<meta charset="utf-8">
<title>Vernac Law – Business Card</title>
<link rel="stylesheet" href="https://fonts.googleapis.com/css2?family=Cinzel:wght@400;600&family=Tinos&display=swap">
<style>
  :root {
    --teal: #13899a;
    --white: #ffffff;
    --ink: #555555;
    --backdrop: #4b4b4b;
  }
  * { margin: 0; padding: 0; box-sizing: border-box; }
  html, body { width: 1105px; height: 1200px; overflow: hidden; }
  body { background: var(--backdrop); position: relative; }

  .card {
    position: absolute;
    left: 196px;
    width: 720px;
    height: 411px;
    overflow: hidden;
  }
  .card--front { top: 146px; background: var(--white); }
  .card--back  { top: 602px; background: var(--teal); color: var(--white); text-align: center; }

  .name-band {
    position: absolute;
    left: 0; top: 62px;
    width: 100%; height: 80px;
    background: var(--teal);
    color: var(--white);
    font-family: "Cinzel", serif;
  }
  .name-band__name {
    position: absolute; left: 36px; top: 8px;
    font-size: 31px; font-weight: 600; letter-spacing: 1px;
  }
  .name-band__title {
    position: absolute; left: 36px; top: 46px;
    font-size: 21px; letter-spacing: 1px;
  }

  .firm-name {
    position: absolute; right: 34px; top: 180px;
    font-family: "Cinzel", serif;
    font-size: 34px; letter-spacing: 1px;
    color: var(--teal);
  }

  .contact {
    position: absolute;
    display: flex; align-items: center; gap: 13px;
    font-family: "Tinos", serif;
    font-size: 20px; color: var(--ink);
  }
  .contact svg { width: 18px; height: 18px; fill: var(--teal); flex: none; }
  .contact--phone { left: 39px; top: 306px; }
  .contact--email { left: 39px; top: 337px; }
  .contact--web   { right: 38px; top: 337px; }

  .back-name {
    position: absolute; left: 0; right: 0; top: 128px;
    font-family: "Cinzel", serif;
    font-size: 58px; letter-spacing: 2px;
  }
  .tagline {
    position: absolute; left: 0; right: 0; top: 315px;
    font-family: "Cinzel", serif;
    font-size: 22px; letter-spacing: 1.5px;
  }
  .services {
    position: absolute; left: 0; right: 0; top: 348px;
    font-family: "Tinos", serif;
    font-size: 20px;
  }
</style>
</head>
<body>

<section class="card card--front" aria-label="Business card front">
  <div class="name-band">
    <div class="name-band__name">Maren Vernac</div>
    <div class="name-band__title">Trial Lawyer</div>
  </div>

  <div class="firm-name">Vernac Law</div>

  <div class="contact contact--phone">
    <svg viewBox="0 0 24 24" aria-hidden="true"><path d="M6.6 10.8c1.4 2.8 3.8 5.1 6.6 6.6l2.2-2.2c.3-.3.7-.4 1-.2 1.1.4 2.3.6 3.6.6.6 0 1 .4 1 1V20c0 .6-.4 1-1 1C10.6 21 3 13.4 3 4c0-.6.4-1 1-1h3.5c.6 0 1 .4 1 1 0 1.3.2 2.5.6 3.6.1.3 0 .7-.2 1l-2.3 2.2z"/></svg>
    <span>(555) 014-2286</span>
  </div>
  <div class="contact contact--email">
    <svg viewBox="0 0 24 24" aria-hidden="true"><path d="M2 5h20v14H2z M2 5l10 8 10-8" /><path d="M3 6l9 7 9-7v-.5H3z" fill="#fff"/></svg>
    <span>maren@vernac-law.example</span>
  </div>
  <div class="contact contact--web">
    <svg viewBox="0 0 24 24" aria-hidden="true"><circle cx="12" cy="12" r="10"/><path d="M12 2c-3 3-3 17 0 20M12 2c3 3 3 17 0 20M2.5 9h19M2.5 15h19" stroke="#fff" stroke-width="1.3" fill="none"/></svg>
    <span>www.vernac-law.example</span>
  </div>
</section>

<section class="card card--back" aria-label="Business card back">
  <div class="back-name">Vernac Law</div>
  <div class="tagline">RELATIONSHIPS. RESPECT. RESULTS.</div>
  <div class="services">Criminal Law,&nbsp; Civil Litigation/Personal Injury, Restraining</div>
</section>

</body>
</html>
```